Ward Compass Business Card Design*

We need a business card design for our company Ward Compass. Our company is specialized in providing online consulting services regarding medical institutions, hospitals and doctors. We work with patients worldwide looking to choose between healthcare providers. We have a website you may use as a reference, where we list doctors and clinics worldwide. So we target Medical providers as well as patients worldwide.
Target Market(s)
Medical Providers and patients around the world
Industry/Entity Type
Medical
Contact Information for Business Card
Salwa Kettani
CEO
+90 612 348 2175
info@wardcompass.example
www.wardcompass.example
14 Annakhil 7 H.R.B. Rabat, Morocco
Requirements
Must have
- Company logo/name on one full side, personal info and smaller logo and company name on the other side.
Nice to have
- Smart and elegant design

```html
<!DOCTYPE html>
<html lang="en">
<head>
<meta charset="utf-8">
<title>Ward Compass — Business Card</title>
<link href="https://fonts.googleapis.com/css2?family=Montserrat:wght@300;400;500;700&display=swap" rel="stylesheet">
<style>
  :root {
    --bg: #e9ebee;
    --blue-light: #2a9fd6;
    --blue-mid: #2887c8;
    --blue-deep: #2672b6;
    --navy: #1d3f6a;
    --ink: #3c3c3c;
    --grey: #8a8a8a;
    --white: #ffffff;
  }
  * { box-sizing: border-box; margin: 0; padding: 0; }
  html, body {
    width: 1200px; height: 874px; overflow: hidden;
    background: var(--bg);
    font-family: "Montserrat", Arial, sans-serif;
  }
  .canvas { position: relative; width: 1200px; height: 874px; }

  .card {
    position: absolute;
    width: 620px; height: 354px;
    border-radius: 26px;
    overflow: hidden;
    box-shadow: 0 14px 30px rgba(0,0,0,0.18);
  }

  /* Front side */
  .card-front {
    left: 80px; top: 70px;
    background: radial-gradient(ellipse at 50% 45%, var(--blue-light) 0%, var(--blue-mid) 45%, var(--blue-deep) 100%);
    display: flex; flex-direction: column; align-items: center; justify-content: center;
    gap: 26px;
  }
  .brand-dot {
    width: 96px; height: 96px; border-radius: 50%;
    border: 16px solid var(--white);
  }
  .brand-name {
    color: var(--white);
    font-weight: 500;
    font-size: 40px;
    letter-spacing: 2px;
  }

  /* Back side */
  .card-back {
    left: 500px; top: 450px;
    background: var(--white);
  }
  .back-brand {
    position: absolute; left: 46px; top: 110px;
    display: flex; flex-direction: column; align-items: center; gap: 16px;
    width: 220px;
  }
  .back-brand .brand-dot {
    width: 70px; height: 70px; border: 12px solid var(--navy);
  }
  .back-brand .brand-name {
    color: var(--navy); font-size: 20px; letter-spacing: 1px;
  }

  .identity {
    position: absolute; left: 320px; top: 62px;
    padding-left: 18px;
    border-left: 1.5px solid var(--blue-light);
  }
  .person-name { font-size: 24px; line-height: 1.1; }
  .person-name .first { color: var(--blue-light); font-weight: 700; }
  .person-name .last { color: var(--grey); font-weight: 300; }
  .person-role { color: var(--ink); font-size: 14px; margin-top: 5px; }

  .contacts {
    position: absolute; left: 320px; top: 160px;
    padding-left: 18px;
    border-left: 1.5px solid var(--blue-light);
    list-style: none;
    display: flex; flex-direction: column; gap: 8px;
  }
  .contacts li {
    display: flex; align-items: center; gap: 10px;
    color: var(--ink); font-size: 14px;
  }
  .contacts svg { width: 15px; height: 15px; fill: var(--blue-deep); flex: none; }

  .footer-band {
    position: absolute; left: 0; right: 0; bottom: 0; height: 14px;
    display: flex; gap: 4px;
  }
  .footer-band .band-dark { flex: 1.3; background: var(--blue-deep); }
  .footer-band .band-light { flex: 1; background: var(--blue-light); }
</style>
</head>
<body>
<main class="canvas">
  <section class="card card-front" aria-label="Card front">
    <span class="brand-dot"></span>
    <span class="brand-name">WARD COMPASS</span>
  </section>

  <section class="card card-back" aria-label="Card back">
    <div class="back-brand">
      <span class="brand-dot"></span>
      <span class="brand-name">WARD COMPASS</span>
    </div>

    <div class="identity">
      <p class="person-name"><span class="first">SALWA</span> <span class="last">KETTANI</span></p>
      <p class="person-role">CEO of WardCompass</p>
    </div>

    <ul class="contacts">
      <li>
        <svg viewBox="0 0 24 24" aria-hidden="true"><path d="M6.6 10.8a15.1 15.1 0 0 0 6.6 6.6l2.2-2.2a1 1 0 0 1 1-.25 11.4 11.4 0 0 0 3.6.57 1 1 0 0 1 1 1V20a1 1 0 0 1-1 1A17 17 0 0 1 3 4a1 1 0 0 1 1-1h3.5a1 1 0 0 1 1 1c0 1.25.2 2.45.57 3.57a1 1 0 0 1-.25 1z"/></svg>
        +90 612 348 2175
      </li>
      <li>
        <svg viewBox="0 0 24 24" aria-hidden="true"><path d="M2 5h20v14H2z M2 5l10 8 10-8" fill="var(--blue-deep)" stroke="#fff" stroke-width="1.5"/></svg>
        info@wardcompass.example
      </li>
      <li>
        <svg viewBox="0 0 24 24" aria-hidden="true"><circle cx="12" cy="12" r="10"/><path d="M2 12h20M12 2c3 3 3 17 0 20M12 2c-3 3-3 17 0 20M4 7h16M4 17h16" stroke="#fff" stroke-width="1.3" fill="none"/></svg>
        www.wardcompass.example
      </li>
    </ul>

    <div class="footer-band">
      <span class="band-dark"></span>
      <span class="band-light"></span>
    </div>
  </section>
</main>
</body>
</html>
```